New Business Card Design

We need a business card design for a new company based in Sydney called "Haven and Hue". This is an online buisness which will have an online store providing imported homewares.
We are looking for something that is different, perhaps even in shape and using the logo that was designed by Pixel Harbor.

Attached document is a basic example I want to see more creative versions.

Target Market(s)

Homewares, Interior Design

Industry/Entity Type

Business

Contact Information for Business Card

Company Logo
Company Name
Industry area
Name
Position
Phone
Email
Website
Motto

Requirements
Must have
• Logo
Nice to have
• Social website logos - Chatterloop, Glimmoraly, Quibbly, Boardlyne, Veltrix+

```html
<!DOCTYPE html>
<html lang="en">
<head>
<meta charset="utf-8">
<title>Haven and Hue – Business Card</title>
<link href="https://fonts.googleapis.com/css2?family=Lato:wght@400;700;900&display=swap" rel="stylesheet">
<style>
  :root {
    --page-bg: #ece7e0;
    --card-top: #f3f2f0;
    --card-bottom: #dcd9d5;
    --brown: #7b4a16;
    --gold: #b07a3a;
    --ink: #1f1f1f;
    --band: #1b1b1b;
    --band-light: #3a3a3a;
  }
  * { margin: 0; padding: 0; box-sizing: border-box; }
  html, body {
    width: 1200px; height: 970px; overflow: hidden;
    background: var(--page-bg);
    font-family: "Lato", Arial, sans-serif;
  }
  .business-card {
    position: absolute; left: 172px; top: 272px;
    width: 856px; height: 474px;
    border-radius: 16px; overflow: hidden;
    background: linear-gradient(160deg, var(--card-top), var(--card-bottom));
    box-shadow: 0 6px 24px rgba(0,0,0,0.18);
  }
  .brand {
    position: absolute; left: 50px; top: 180px; width: 350px;
    display: flex; align-items: center; justify-content: center; gap: 14px;
  }
  .brand-dot {
    width: 22px; height: 22px; border-radius: 50%;
    background: var(--gold); flex: none;
  }
  .brand-name {
    font-size: 40px; font-weight: 700; color: var(--ink);
    white-space: nowrap;
  }
  .divider {
    position: absolute; left: 425px; top: 80px;
    width: 2px; height: 262px; background: var(--gold);
  }
  .contact { position: absolute; left: 441px; top: 88px; color: var(--ink); }
  .person-name { font-size: 29px; font-weight: 900; color: var(--brown); line-height: 34px; }
  .person-role { font-size: 24px; line-height: 30px; }
  .address { margin-top: 30px; font-size: 21px; line-height: 28px; }
  .details { margin-top: 12px; list-style: none; font-size: 21px; line-height: 29px; }
  .details li { display: flex; align-items: center; gap: 12px; }
  .details svg { width: 22px; height: 22px; flex: none; }
  .phone-number { letter-spacing: 4px; }
  .gold-rule {
    position: absolute; left: 0; right: 0; top: 414px;
    height: 3px; background: var(--gold);
  }
  .footer-band {
    position: absolute; left: 0; right: 0; top: 421px; bottom: 0;
    background: linear-gradient(90deg, var(--band), var(--band-light) 20%, var(--band) 45%, var(--band));
  }
  .social-list {
    position: absolute; right: 38px; top: 0; height: 100%;
    display: flex; align-items: center; gap: 14px; list-style: none;
  }
  .social-list li {
    display: flex; align-items: center; gap: 5px;
    font-size: 12px; font-weight: 700; color: var(--gold);
  }
  .social-list li::before {
    content: ""; width: 10px; height: 10px; border-radius: 50%;
    background: var(--gold);
  }
</style>
</head>
<body>
  <div class="business-card">
    <div class="brand">
      <span class="brand-dot"></span>
      <span class="brand-name">Haven and Hue</span>
    </div>

    <div class="divider"></div>

    <div class="contact">
      <p class="person-name">Marco Ellery</p>
      <p class="person-role">Director</p>
      <p class="address">Unit 0, Linden Avenue<br>Havenfield 1234 Queensland AU</p>
      <ul class="details">
        <li>
          <svg viewBox="0 0 24 24" aria-hidden="true"><path fill="#7b4a16" d="M3 9c0-3 4-5 9-5s9 2 9 5v1h-5V8.5c-1.5-.5-6.5-.5-8 0V10H3z"/><rect x="5" y="12" width="14" height="9" rx="2" fill="#7b4a16"/></svg>
          <span class="phone-number">0798765432</span>
        </li>
        <li>
          <svg viewBox="0 0 24 24" aria-hidden="true"><rect x="2" y="5" width="20" height="14" fill="#7b4a16"/><path d="M2 5l10 8 10-8" fill="none" stroke="#f0ede9" stroke-width="1.6"/></svg>
          <span>me@havenandhue.com.au</span>
        </li>
        <li>
          <svg viewBox="0 0 24 24" aria-hidden="true"><circle cx="12" cy="12" r="10" fill="#7b4a16"/><g fill="none" stroke="#f0ede9" stroke-width="1.4"><ellipse cx="12" cy="12" rx="4.5" ry="10"/><path d="M2 12h20M4 7h16M4 17h16"/></g></svg>
          <span>www.havenandhue.com.au</span>
        </li>
      </ul>
    </div>

    <div class="gold-rule"></div>
    <div class="footer-band">
      <ul class="social-list">
        <li>Chatterloop</li>
        <li>Quibbly</li>
        <li>Glimmoraly</li>
        <li>Boardlyne</li>
        <li>Veltrix+</li>
      </ul>
    </div>
  </div>
</body>
</html>
```